Business Card design for law firm = Brightvale Australia

We are seeking a new design for our business cards.
We are keeping our logo, which is attached.
We need space for
Name
Title
Address is , which is
Level 7
214 Marlowe Street
Sydney NSW 2047
Phone :
Mobile :
Fax :
Email :
DX :
website www.brightvale-example.com.au

Industry/Entity Type

Law Firm / Banking and Finance

Contact Information for Business Card

We are seeking a new design for our business cards. We are keeping our logo. We need space for Name Title Address is Level 7 214 Marlowe Street Sydney NSW 2047 Phone Mobile Fax Email DX website www.brightvale-example.com.au

Colors
0054AA
0677BA
7BADD7
CADEEF
E8F1F8

Requirements
Must have
• see our website for general feel www.brightvale-example.com.au

```html
<!DOCTYPE html>
<html lang="en">
<head>
<meta charset="utf-8">
<title>Brightvale Business Card</title>
<link href="https://fonts.googleapis.com/css2?family=EB+Garamond:wght@400&display=swap" rel="stylesheet">
<style>
  :root {
    --backdrop: #2b2b2c;
    --card-dark: #1a1b1d;
    --card-light: #2c2d30;
    --accent-blue: #2f4c9f;
    --accent-cyan: #0a8ec6;
    --text-light: #e6e6e6;
    --text-dim: #4a4c50;
  }
  * { margin: 0; padding: 0; box-sizing: border-box; }
  html, body {
    width: 1200px; height: 1138px; overflow: hidden;
    background: var(--backdrop);
  }
  .canvas { position: relative; width: 1200px; height: 1138px; }
  .card {
    position: absolute; width: 620px; height: 375px;
    border-radius: 16px; overflow: hidden;
    background: linear-gradient(160deg, var(--card-dark) 0%, var(--card-dark) 40%, var(--card-light) 100%);
    box-shadow: 0 6px 14px rgba(0,0,0,0.35);
  }
  .card--front { left: 272px; top: 184px; }
  .card--back { left: 274px; top: 606px; }

  .brand {
    position: absolute; display: flex; align-items: center; gap: 14px;
    white-space: nowrap;
  }
  .brand-dot {
    flex: none; width: 12px; height: 12px; border-radius: 50%;
    background: var(--accent-blue);
  }
  .brand-name {
    font-family: "EB Garamond", serif; font-weight: 400;
    color: var(--text-light); line-height: 1;
  }
  .card--front .brand {
    left: 0; width: 620px; justify-content: center; top: 150px;
  }
  .card--front .brand-name { font-size: 46px; }

  .front-url {
    position: absolute; left: 0; width: 620px; top: 332px; text-align: center;
    font-family: "EB Garamond", serif; font-size: 15px; letter-spacing: 5.4px;
    color: var(--text-light); white-space: nowrap; line-height: 1;
  }
  .front-bar {
    position: absolute; left: 142px; width: 340px; bottom: 0; height: 7px;
    background: var(--accent-blue);
  }

  .card--back .brand { left: 34px; top: 52px; }
  .card--back .brand-name { font-size: 38px; }

  .person-name {
    position: absolute; left: 34px; top: 209px; font-family: "EB Garamond", serif;
    font-size: 24px; color: var(--accent-blue); line-height: 1; white-space: nowrap;
  }
  .person-title {
    position: absolute; left: 34px; top: 236px; font-family: "EB Garamond", serif;
    font-size: 16px; color: var(--text-light); line-height: 1; white-space: nowrap;
  }
  .contact-row {
    position: absolute; display: flex; align-items: center; gap: 8px;
    font-family: "EB Garamond", serif; font-size: 15px; color: var(--text-light);
    white-space: nowrap; line-height: 1;
  }
  .contact-row svg { width: 13px; height: 13px; flex: none; }
  .contact-row--dim { color: var(--text-dim); }
  .phone { left: 34px; top: 294px; }
  .fax { left: 34px; top: 317px; }
  .email { left: 160px; top: 294px; }
  .web { left: 160px; top: 317px; }
  .address { left: 406px; top: 294px; align-items: flex-start; }
  .address-lines span { display: block; margin-bottom: 8px; }
  .back-bar {
    position: absolute; left: 0; right: 0; bottom: 0; height: 7px;
    background: var(--accent-blue);
  }
</style>
</head>
<body>
<main class="canvas">
  <section class="card card--front" aria-label="Card front">
    <div class="brand">
      <span class="brand-dot"></span>
      <span class="brand-name">Brightvale</span>
    </div>
    <div class="front-url">www.brightvale-example.com.au</div>
    <div class="front-bar"></div>
  </section>

  <section class="card card--back" aria-label="Card back">
    <div class="brand">
      <span class="brand-dot"></span>
      <span class="brand-name">Brightvale</span>
    </div>

    <div class="person-name">Sam Whitford</div>
    <div class="person-title">Managing Director</div>

    <div class="contact-row contact-row--dim phone">
      <svg viewBox="0 0 16 16" aria-hidden="true"><path fill="#0a8ec6" d="M1 5c0-2 3-3 7-3s7 1 7 3v1h-4V5H5v1H1zM3 7h10l1 7H2zM8 9a2 2 0 1 0 0 4 2 2 0 0 0 0-4z"/></svg>
      <span>02 5550 0148</span>
    </div>
    <div class="contact-row contact-row--dim fax">
      <svg viewBox="0 0 16 16" aria-hidden="true"><path fill="#0a8ec6" d="M4 1h8v4H4zM1 6h14v6h-3v3H4v-3H1zM5 10v4h6v-4z"/></svg>
      <span>02 5550 0193</span>
    </div>
    <div class="contact-row email">
      <svg viewBox="0 0 16 16" aria-hidden="true"><path fill="#0a8ec6" d="M1 3h14v10H1z"/><path fill="none" stroke="#1a1b1d" stroke-width="1.3" d="M1.5 3.5 8 9l6.5-5.5M1.5 12.5l5-4.5M14.5 12.5l-5-4.5"/></svg>
      <span>sam@brightvale-example.com.au</span>
    </div>
    <div class="contact-row web">
      <svg viewBox="0 0 16 16" aria-hidden="true"><g fill="none" stroke="#0a8ec6" stroke-width="1.4"><circle cx="8" cy="8" r="6.5"/><ellipse cx="8" cy="8" rx="3" ry="6.5"/><path d="M1.5 8h13"/></g></svg>
      <span>www.brightvale-example.com.au</span>
    </div>
    <div class="contact-row address">
      <svg viewBox="0 0 16 16" aria-hidden="true"><path fill="#0a8ec6" d="M8 1a5 5 0 0 0-5 5c0 4 5 9 5 9s5-5 5-9a5 5 0 0 0-5-5zm0 3a2 2 0 1 1 0 4 2 2 0 0 1 0-4z"/></svg>
      <div class="address-lines">
        <span>Level 7 214 Marlowe St</span>
        <span>Sydney NSW 2047</span>
      </div>
    </div>
    <div class="back-bar"></div>
  </section>
</main>
</body>
</html>
```